Meadowlark Property Review is a leading provider of residential appraisal and home inspection products in S

I need a business card/logo designed that obviously describes my business. We are a residential appraisal and home inspection company in Springfield, MO. We offer residential appraisals, home inspection, pest inspection and radon gas measurement. We have been in business for 18 years and hold state certified residential appraisal licenses and OBREX certified home inspection licenses. I have a logo that I really like and will attach, but would be open to new suggestions. I like more modern designs than traditional and would like a two sided card with our services, licenses and qualifications on the back.

```html
<!DOCTYPE html>
<html lang="en">
<head>
<meta charset="utf-8">
<title>Meadowlark Property Review – Business Card</title>
<link href="https://fonts.googleapis.com/css2?family=Source+Sans+3:ital,wght@0,400;0,600;1,400&display=swap" rel="stylesheet">
<style>
  :root {
    --stage: #3b3b3b;
    --brown: #8c6b43;
    --orange: #f08a1c;
    --white: #ffffff;
    --paper: #f7f7f7;
    --logo-brown: #7d5a35;
  }
  * { margin: 0; padding: 0; box-sizing: border-box; }
  html, body {
    width: 1200px; height: 750px; overflow: hidden;
    background: var(--stage);
    font-family: "Source Sans 3", sans-serif;
  }
  .canvas { position: relative; width: 1200px; height: 750px; }
  .card {
    position: absolute; top: 228px;
    width: 461px; height: 262px; overflow: hidden;
  }
  .card-back { left: 146px; background: var(--brown); color: var(--white); }
  .card-front { left: 618px; background: var(--paper); }
  .card-shape { position: absolute; inset: 0; width: 100%; height: 100%; }

  .contact { position: absolute; left: 29px; top: 22px; }
  .person-name { color: var(--orange); font-weight: 600; font-size: 17px; line-height: 20px; }
  .person-title { font-size: 13px; line-height: 17px; }
  .address { margin-top: 6px; font-size: 11px; line-height: 14px; }
  .contact-list { list-style: none; margin-top: 9px; }
  .contact-list li {
    display: flex; align-items: center; gap: 6px;
    font-size: 11px; line-height: 17.5px;
  }
  .contact-list svg { width: 12px; height: 12px; fill: var(--orange); flex: none; }
  .services { list-style: none; margin-top: 7px; }
  .services li {
    position: relative; padding-left: 13px;
    font-style: italic; font-size: 11.5px; line-height: 15px;
  }
  .services li::before {
    content: ""; position: absolute; left: 0; top: 6px;
    width: 4px; height: 4px; border-radius: 50%; background: var(--orange);
  }

  .brand {
    position: absolute; left: 196px; top: 104px; width: 240px;
    text-align: center; color: var(--logo-brown);
    font-weight: 600; font-size: 21px; line-height: 25px;
  }
</style>
</head>
<body>
<main class="canvas">
  <section class="card card-back" aria-label="Card back with contact details">
    <svg class="card-shape" viewBox="0 0 576 328" preserveAspectRatio="none" aria-hidden="true">
      <polygon points="576,0 576,127 369,328 242,328" fill="var(--white)"/>
    </svg>
    <div class="contact">
      <p class="person-name">Dana Whitfield</p>
      <p class="person-title">CEO/Founder</p>
      <p class="address">214 Linden Court<br>Springfield, Missouri 65804</p>
      <ul class="contact-list">
        <li><svg viewBox="0 0 12 12"><path d="M2.5 0.5l2 2.2-1 1.3c.6 1.6 1.9 2.9 3.5 3.5l1.3-1 2.2 2-1.2 2.2C5.5 10.5 1.5 6.5 1 2z"/></svg>417 555 0182</li>
        <li><svg viewBox="0 0 12 12"><rect x="3" y="0.5" width="6" height="3"/><rect x="0.5" y="4" width="11" height="5" rx="1"/><rect x="3" y="9.5" width="6" height="2"/></svg>417 555 0197</li>
        <li><svg viewBox="0 0 12 12"><path d="M0.5 2.5h11v7h-11z M1.2 3l4.8 3.6L10.8 3z"/></svg>dana@meadowlarkreview.com</li>
        <li><svg viewBox="0 0 12 12"><circle cx="6" cy="6" r="5.5"/></svg>www.meadowlarkreview.com</li>
      </ul>
      <ul class="services">
        <li>Residential appraisals</li>
        <li>Home inspection</li>
        <li>Pest inspection and</li>
        <li>radon gas measurement.</li>
      </ul>
    </div>
  </section>

  <section class="card card-front" aria-label="Card front with company name">
    <svg class="card-shape" viewBox="0 0 576 328" preserveAspectRatio="none" aria-hidden="true">
      <polygon points="0,0 336,328 207,328 0,127" fill="var(--orange)"/>
    </svg>
    <p class="brand">Meadowlark<br>Property Review</p>
  </section>
</main>
</body>
</html>
```